Personal letterhead and stationary

I am looking for someone to design letterhead and stationary set for my personal use. I want something simple and timeless with a little bit of color. I like photography, computers and writing.

```html
<!DOCTYPE html>
<html lang="en">
<head>
<meta charset="utf-8">
<title>Daniel Owen Marsh — Letterhead</title>
<link rel="stylesheet" href="https://fonts.googleapis.com/css2?family=Jost:wght@400&display=swap">
<style>
  :root {
    --canvas: #ffffff;
    --paper: #fdfdfb;
    --paper-edge: #c9c9c9;
    --ink: #111111;
    --accent: #8bab5a;
  }
  html, body {
    margin: 0;
    padding: 0;
    width: 1200px;
    height: 1000px;
    overflow: hidden;
    background: var(--canvas);
  }
  .artboard {
    position: relative;
    width: 1200px;
    height: 1000px;
  }
  .identity {
    position: absolute;
    left: 0;
    top: 0;
  }
  .identity text {
    font-family: "Jost", "Futura", sans-serif;
    font-weight: 400;
    fill: var(--ink);
  }
  .brand-square { fill: var(--accent); }
  .letterhead-sheet {
    position: absolute;
    left: 616px;
    top: 493px;
    width: 467px;
    height: 520px;
    background: var(--paper);
    border: 1px solid var(--paper-edge);
    box-sizing: border-box;
  }
</style>
</head>
<body>
<main class="artboard">
  <div class="letterhead-sheet"></div>

  <svg class="identity" width="1200" height="1000" viewBox="0 0 1200 1000" aria-label="Daniel Owen Marsh identity">
    <!-- primary lockup -->
    <g class="lockup lockup--large">
      <rect class="brand-square" x="74" y="222" width="100" height="100"/>
      <text class="lockup-name" x="218" y="266" font-size="50" textLength="910" lengthAdjust="spacing">DANIEL OWEN MARSH</text>
      <text class="lockup-address" x="222" y="311" font-size="19" textLength="903" lengthAdjust="spacing">2750 DARKROOM AVENUE, SAN LEANDRO, CA 94577</text>
    </g>

    <!-- lockup on letterhead -->
    <g class="lockup lockup--sheet">
      <rect class="brand-square" x="634" y="542" width="41" height="41"/>
      <text class="lockup-name" x="692" y="559" font-size="20" textLength="374" lengthAdjust="spacing">DANIEL OWEN MARSH</text>
      <text class="lockup-address" x="693" y="579" font-size="8.5" textLength="372" lengthAdjust="spacing">2750 DARKROOM AVENUE, SAN LEANDRO, CA 94577</text>
    </g>
  </svg>
</main>
</body>
</html>
```